Hello my name is Colin, I am Starting a business called Lumen Wellness and fitness and am in need of a memorable business card.
It is a personal training studio. I have added the logo that i would like to be on the left center om my business card. i would like room left up the top for a heading sentence such as. "Is your body shocking for all the wrong reasons". there must be room left on the right of the logo below the main heading for 3 sub headings.
then under those 3 headings and logo room for another larger heading eg. "give me a call and learn how to eat chocolate, drink bear and have great sex". in what room is left i would like to be used for my contact details, use I'm Colin Ferrante your fitness expert on the left then on the right Phone, Email and website space in at least 12 Point. Very specific i know :) now onto the back, for the back i would like an eye catching graphic and room for one main headline and 3 bullet points centered just write anything i will choose what to put in them when i pick a winner. Thank you very much for sticking through all of that :) i appreciate you taking the time to read it and hopefully undergo designing me a business card.
I can't wait to see the designs!

Target Market(s)

slightly more towards females although it would probably be best if it was targeted towards both sexes

Industry/Entity Type

Training

Requirements
Nice to have
• I would love to see if anyone could come up with a design that would really make my card stand out and be memorable.
Should not have
• tacky fitness photos of abs and muscles etc.

```html
<!DOCTYPE html>
<html lang="en">
<head>
<meta charset="utf-8">
<title>Lumen Wellness and fitness — Business Card</title>
<link rel="stylesheet" href="https://fonts.googleapis.com/css2?family=Questrial&family=Open+Sans:wght@400&display=swap">
<style>
  :root {
    --stage: #e9e6e1;
    --card: #ffffff;
    --brand-blue: #1b4f87;
    --brand-blue-deep: #123c6a;
    --band-start: #1d5189;
    --band-end: #0f3a66;
    --ink: #3a3a3a;
    --ink-soft: #555555;
    --white: #ffffff;
  }
  * { box-sizing: border-box; margin: 0; padding: 0; }
  html, body { width: 1200px; height: 788px; overflow: hidden; }
  body {
    position: relative;
    background: var(--stage);
    font-family: "Questrial", "Century Gothic", sans-serif;
    color: var(--ink);
  }
  .side-label {
    position: absolute;
    font-family: "Open Sans", Arial, sans-serif;
    font-size: 20px;
    color: #222;
  }
  .card {
    position: absolute;
    width: 524px;
    height: 300px;
    background: var(--card);
    border-radius: 20px;
    overflow: hidden;
    box-shadow: 0 4px 14px rgba(0,0,0,0.18);
  }
  .card > * { position: absolute; }
  .figures {
    background: linear-gradient(180deg, #2a5f98 0%, #1b4f87 55%, #133f6d 100%);
    border-radius: 40px 40px 6px 6px;
  }
  .tagline { font-size: 13px; color: var(--ink); white-space: nowrap; }
  .brand-name { color: var(--brand-blue); line-height: 1; white-space: nowrap; }
  .brand-sub { color: var(--brand-blue); line-height: 1; white-space: nowrap; }

  /* Front */
  .front { left: 338px; top: 75px; }
  .front .tagline { right: 24px; top: 18px; }
  .front .brand-name { right: 24px; top: 48px; font-size: 58px; }
  .front .brand-sub { right: 32px; top: 114px; font-size: 15px; }
  .front .holder { right: 24px; top: 157px; text-align: right; color: var(--brand-blue); font-size: 13px; line-height: 18px; }
  .front .figures { left: 24px; top: 8px; width: 112px; height: 192px; }
  .contact-band {
    left: 0; top: 200px; width: 524px; height: 100px;
    background: linear-gradient(90deg, var(--band-start), var(--band-end));
    color: var(--white);
  }
  .contact-list { position: absolute; left: 24px; top: 10px; list-style: none; }
  .contact-list li { display: flex; align-items: center; height: 26px; font-size: 19px; }
  .contact-list svg { width: 14px; height: 14px; margin-right: 12px; }
  .pitch {
    position: absolute; right: 24px; top: 23px;
    text-align: right; font-size: 14.5px; line-height: 20px;
  }

  /* Back 1 */
  .back-one { left: 54px; top: 446px; }
  .back-one .figures { left: 42px; top: 20px; width: 146px; height: 262px; }
  .back-one .brand-name { left: 254px; top: 20px; font-size: 36px; }
  .back-one .brand-sub { left: 258px; top: 56px; font-size: 10px; }
  .points { left: 258px; top: 117px; list-style: none; font-family: "Open Sans", Arial, sans-serif; font-size: 15.5px; color: #111; }
  .points li { position: relative; padding-left: 25px; height: 34px; }
  .points li::before { content: ""; position: absolute; left: 0; top: 8px; width: 6px; height: 6px; background: #111; }
  .back-one .web { left: 256px; top: 253px; font-size: 19px; color: var(--ink-soft); }

  /* Back 2 */
  .back-two { left: 621px; top: 441px; }
  .back-two .tagline { left: 0; width: 524px; top: 20px; text-align: center; }
  .back-two .brand-name { left: 0; width: 524px; top: 78px; text-align: center; font-size: 96px; }
  .back-two .brand-sub { left: 0; width: 524px; top: 180px; text-align: center; font-size: 22px; }
  .back-two .web { left: 0; width: 524px; top: 252px; text-align: center; font-size: 20px; letter-spacing: 4px; color: var(--ink-soft); }
</style>
</head>
<body>

  <span class="side-label" style="left:572px; top:34px;">Front</span>
  <section class="card front">
    <p class="tagline">Is your body shocking for all the wrong reasons</p>
    <div class="figures" role="img" aria-label="Blue silhouettes of a man in a suit and a woman standing"></div>
    <p class="brand-name">Lumen</p>
    <p class="brand-sub">Wellness and fitness</p>
    <p class="holder">Colin Ferrante<br>Your Fitness Expert</p>
    <div class="contact-band">
      <ul class="contact-list">
        <li><svg viewBox="0 0 14 14" aria-hidden="true"><circle cx="7" cy="7" r="6" fill="none" stroke="#fff" stroke-width="1.4"/><path d="M4.5 4 L6 4 L6.6 5.8 L5.8 6.4 Q6.6 8 7.8 8.6 L8.4 7.8 L10 8.4 L10 9.8 Q6.6 10 4.4 5.6 Z" fill="#fff"/></svg>+12 345 67890</li>
        <li><svg viewBox="0 0 14 14" aria-hidden="true"><path d="M1 5 L7 1.5 L13 5 L13 12 L1 12 Z" fill="#fff"/><path d="M1.5 5.5 L7 9 L12.5 5.5" fill="none" stroke="#1b4f87" stroke-width="1.2"/></svg>info@website.com</li>
        <li><svg viewBox="0 0 14 14" aria-hidden="true"><circle cx="7" cy="7" r="6" fill="none" stroke="#fff" stroke-width="1.3"/><ellipse cx="7" cy="7" rx="2.6" ry="6" fill="none" stroke="#fff" stroke-width="1"/><path d="M1 7 H13 M2 4 H12 M2 10 H12" stroke="#fff" stroke-width="1"/></svg>www.website.com</li>
      </ul>
      <p class="pitch">Give me a call and learn<br>how to eat chocolate, drink<br>bear and have great sex</p>
    </div>
  </section>

  <span class="side-label" style="left:285px; top:405px;">Back - 1</span>
  <section class="card back-one">
    <div class="figures" role="img" aria-label="Large blue silhouettes of a man in a suit and a woman standing"></div>
    <p class="brand-name">Lumen</p>
    <p class="brand-sub">Wellness and fitness</p>
    <ul class="points">
      <li>Lorem Ipsum has been ...</li>
      <li>Lorem Ipsum has been ...</li>
      <li>Lorem Ipsum has been ...</li>
    </ul>
    <p class="web">www.website.com</p>
  </section>

  <span class="side-label" style="left:857px; top:405px;">Back - 2</span>
  <section class="card back-two">
    <p class="tagline">Is your body shocking for all the wrong reasons</p>
    <p class="brand-name">Lumen</p>
    <p class="brand-sub">Wellness and fitness</p>
    <p class="web">www.website.com</p>
  </section>

</body>
</html>
```